Wordpress - For IT, Cloud/Hosting, Residential/Commercial Construction Services

We are a holding company for service companies. We want the current Wordpress site modified or a new wordpress site completed. We want this site to be the parent website, that then has pull down menus linking to our other website (currently http://brightwallfix.com, http://q7v.host and would like it to be easy and fluid as we acquire more companies as we have with TKLS, Inc., B&J Construction, Brightwall Fix etc. Model after sites like Pemrose.com, Tallowbine.com, QDV.com,.vanterelm.com

------

The parent is the main site q7v Corp. Below that are sub corps and DBAs. q7v Corp stands for Quick 7 Venture Corp. q7v Offers IT manages services, 24x7 support, Monitoring NOC, Remote Hands, Onsite support services. We have acquired TKLS, Inc, B & J Construction, BrightwallFix.com. We plan to acquire/spin up many companies that offer service, support and installation offerings and will all be known as an q7v Corp Company for branding purposes. We recently had our logo done, but then ran it through 3d glass as we like the look better than the original works. We have original files in vector, but not the 3D galss door render.

Target Market(s)

IT Server and Desktop Support. Construction. Mold Remediation. Mergers and Acquisitions.

Industry/Entity Type

It Company

Coding

Coded - Design and coding required

Font styles to use
Sans Serif

Colors
0792cd

Requirements
Must have
• Clean interface. Modern design. Mobile device and multi browser support. Must be for Wordpress. Job posting with resume submission module.Hook to our Web hosting portal (Tormund) API into VexaLine Reseller portal, customer portal to allow payments to their account etc.. Easy to edit. Easy to add to, Press Release Section, Investor Relations etc.
Should not have
• Slow loading. Played out design. Over use of stock images. Copied from a competitor or something point to such.

```html
<!DOCTYPE html>
<html lang="en">
<head>
<meta charset="utf-8">
<title>q7v Corp</title>
<link href="https://fonts.googleapis.com/css2?family=Roboto:wght@300;400;500;700&family=Montserrat:wght@500;600&display=swap" rel="stylesheet">
<style>
:root{
  --primary:#0792cd;
  --navy:#1a5ea8;
  --footer:#1d6cb0;
  --bar:#2aa9e0;
  --button:#2ab0e0;
  --ink:#222;
  --body:#444;
  --muted:#777;
  --page:#f2f2f2;
  --white:#fff;
}
*{margin:0;padding:0;box-sizing:border-box}
html,body{width:1200px;height:2970px;overflow:hidden}
body{position:relative;background:var(--page);font-family:"Roboto",sans-serif;color:var(--body)}
.abs{position:absolute}

/* header */
.site-header{left:0;top:0;width:1200px;height:102px;background:var(--white);z-index:2}
.brand{left:110px;top:34px;color:var(--navy);font-size:32px;font-weight:700;line-height:36px;white-space:nowrap}
.main-nav{left:485px;top:45px;display:flex;font-size:14.5px;color:#333}
.main-nav span{margin-right:30px}
.main-nav .active{color:var(--primary);font-weight:500}
.dropdown{left:733px;top:78px;width:156px;height:152px;background:var(--navy);padding-top:16px;z-index:5}
.dropdown div{color:#fff;font-size:11.5px;height:41px;padding-left:22px;line-height:16px}
.dropdown div::before{content:"›";margin-right:14px;font-size:15px}

/* hero */
.hero{left:0;top:102px;width:1200px;height:456px;background:linear-gradient(100deg,#0e2c4d 0%,#1f5b8c 30%,#2d6f9e 55%,#173e63 80%,#0b2440 100%)}
.hero-title{left:0;top:288px;width:1200px;text-align:center;color:#fff;font-size:44px;font-weight:500}
.hero-sub{left:0;top:340px;width:1200px;text-align:center;color:#fff;font-size:20px;font-weight:500}

/* welcome */
.section-title{left:0;width:1200px;text-align:center;color:var(--ink);font-size:28px;font-weight:300}
.section-title b{font-weight:700}
.section-title .accent{color:var(--primary);font-weight:400}
.welcome-text{left:135px;top:640px;width:930px;text-align:center;font-size:12px;line-height:26px;color:#555}
.rule{left:135px;top:752px;width:930px;height:1px;background:#ccc}

/* services */
.service-card{top:852px;width:226px;height:318px;background:var(--white);box-shadow:0 1px 4px rgba(0,0,0,.12);text-align:center}
.service-card h3{font-size:16px;font-weight:400;color:#333;margin-top:32px}
.service-card svg{margin-top:28px}
.service-card p{font-size:11.5px;line-height:19px;color:#444;margin:20px 14px 0}
.btn{display:inline-block;background:var(--button);color:#fff;font-size:13px;font-weight:500;padding:8px 20px;border-radius:2px}
.btn.dark{background:var(--navy)}
.service-card .btn{margin-top:16px}
.chev{font-size:26px;color:#333;font-weight:700}

/* clients */
.clients{left:0;top:1222px;width:1200px;height:323px;background:linear-gradient(90deg,#d9d6d1 0%,#eeecea 35%,#e8e7e5 60%,#dadcde 100%)}
.client-row{left:160px;top:1380px;display:flex;align-items:center;gap:44px;font-size:26px;font-weight:500;color:#5a5a5a}
.client-row .sq{display:inline-block;width:40px;height:40px;background:#5a5a5a;vertical-align:middle;margin-right:10px}

/* story */
.story-title{left:110px;top:1652px;font-size:26px;font-weight:400;color:var(--ink)}
.story-text{left:110px;top:1700px;width:475px;font-size:13px;line-height:30.5px;color:#333}
.story-image{left:612px;top:1602px;width:476px;height:420px;background:linear-gradient(135deg,#a9b4bd,#4c5a69 50%,#2b3440)}

/* blog */
.blog-card{top:2183px;width:302px;height:370px;background:var(--white);box-shadow:0 1px 4px rgba(0,0,0,.12)}
.blog-image{margin:4px;width:294px;height:192px}
.blog-card h4{font-family:"Montserrat",sans-serif;font-weight:600;font-size:16px;color:#222;margin:28px 22px 0}
.blog-card p{font-size:11.5px;line-height:20px;color:#666;margin:12px 22px 0}
.blog-meta{margin:18px 22px 0;padding-top:14px;border-top:1px solid #e6e6e6;font-size:11px;color:#444}
.blog-meta .more{color:var(--primary);font-weight:500}
.date-badge{left:6px;top:6px;width:48px;height:60px;background:var(--bar);color:#fff;text-align:center;font-size:20px;line-height:26px;padding-top:4px}
.date-badge small{display:block;font-size:12px;line-height:16px}

/* footer */
.site-footer{left:0;top:2610px;width:1200px;height:310px;background:var(--footer);color:#fff}
.footer-head{font-size:14.5px;font-weight:400;color:#fff}
.quick-links div{font-size:11.5px;height:31px}
.quick-links div::before{content:"›";margin-right:10px}
.footer-small{font-size:12px;line-height:19px}
.social{width:32px;height:32px;border-radius:50%;background:#17467c;color:#fff;font-size:10px;font-weight:500;text-align:center;line-height:32px}
.footer-brand{left:946px;top:150px;color:#fff;font-size:28px;font-weight:700;line-height:32px;white-space:nowrap}
.bottom-bar{left:0;top:2920px;width:1200px;height:50px;background:var(--bar);color:#fff;text-align:center;font-size:12px;line-height:50px}
</style>
</head>
<body>

<header class="site-header abs">
  <div class="brand abs">q7v Corp</div>
  <nav class="main-nav abs">
    <span class="active">Home</span><span>About Us</span><span>Services</span><span>Companies ▾</span><span>Blog</span><span>Testimonials</span><span>Contact Us</span>
  </nav>
</header>

<section class="hero abs" role="img" aria-label="Data centre aisle with a person among server racks"></section>
<div class="dropdown abs"><div>Sample Link1</div><div>Sample Link1</div><div>Sample Link1</div></div>
<div class="hero-title abs">Q7V Corp</div>
<div class="hero-sub abs">is a Ardentix and Tallowbine IT Solution Provider.</div>
<svg class="abs" style="left:99px;top:302px" width="34" height="34"><circle cx="17" cy="17" r="17" fill="rgba(255,255,255,.55)"/><path d="M20 10 L13 17 L20 24" stroke="#333" stroke-width="3" fill="none"/></svg>
<svg class="abs" style="left:1068px;top:302px" width="34" height="34"><circle cx="17" cy="17" r="17" fill="rgba(255,255,255,.55)"/><path d="M14 10 L21 17 L14 24" stroke="#333" stroke-width="3" fill="none"/></svg>

<h1 class="section-title abs" style="top:593px">Welcome To <b>Q7V</b> <span class="accent">Corp.</span></h1>
<p class="welcome-text abs">Sed ut perspiciatis unde omnis iste natus error sit voluptatem accusantium doloremque laudantium, totam rem aperiam, eaque ipsa quae ab illo inventore veritatis et quasi architecto beatae vitae dicta sunt explicabo. Nemo enim ipsam voluptatem quia voluptas sit aspernatur aut odit aut fugit, sed quia consequuntur magni dolores eos qui ratione voluptatem sequi nesciunt. Neque porro quisquam est, qui dolorem ipsum quia dolor sit amet, consectetur,</p>
<div class="rule abs"></div>

<h2 class="section-title abs" style="top:780px">Our <b>Services</b></h2>
<div class="chev abs" style="left:76px;top:978px">‹</div>
<div class="chev abs" style="left:1114px;top:978px">›</div>

<article class="service-card abs" style="left:112px">
  <h3>Information Technology</h3>
  <svg width="80" height="64" viewBox="0 0 80 64" fill="none" stroke="var(--primary)" stroke-width="2.5"><rect x="14" y="8" width="52" height="36" rx="3"/><path d="M6 50 H74 L70 56 H10 Z"/><path d="M30 38 H50"/></svg>
  <p>Lorem ipsum dolor sit amet, consectetur adipiscing elit, sed do eiusmod tempor incididunt ut labore et dolore magna aliqua.</p>
  <span class="btn dark">Read more</span>
</article>
<article class="service-card abs" style="left:360px">
  <h3>Cloud/Hosting</h3>
  <svg width="80" height="64" viewBox="0 0 80 64" fill="none" stroke="var(--primary)" stroke-width="2.5"><path d="M18 34 a12 12 0 0 1 4-22 a16 16 0 0 1 30 2 a11 11 0 0 1 8 20 Z"/><path d="M34 16 V30 M30 20 L34 16 L38 20 M46 30 V16 M42 26 L46 30 L50 26"/><rect x="22" y="38" width="36" height="8" rx="2"/><rect x="22" y="48" width="36" height="8" rx="2"/></svg>
  <p>Lorem ipsum dolor sit amet, consectetur adipiscing elit, sed do eiusmod tempor incididunt ut labore et dolore magna aliqua.</p>
  <span class="btn">Read more</span>
</article>
<article class="service-card abs" style="left:610px">
  <h3>Home/Commercial</h3>
  <svg width="80" height="64" viewBox="0 0 80 64" fill="none" stroke="var(--primary)" stroke-width="2.5"><rect x="22" y="6" width="22" height="54"/><rect x="44" y="20" width="16" height="40"/><path d="M28 14 H38 M28 22 H38 M28 30 H38 M28 38 H38 M28 46 H38 M49 28 H55 M49 36 H55 M49 44 H55 M16 60 H66"/></svg>
  <p>Lorem ipsum dolor sit amet, consectetur adipiscing elit, sed do eiusmod tempor incididunt ut labore et dolore magna aliqua.</p>
  <span class="btn">Read more</span>
</article>
<article class="service-card abs" style="left:866px">
  <h3>Construction</h3>
  <svg width="80" height="64" viewBox="0 0 80 64" fill="none" stroke="var(--primary)" stroke-width="2.5"><circle cx="32" cy="36" r="12" stroke-dasharray="5 3" stroke-width="5"/><circle cx="32" cy="36" r="5"/><circle cx="54" cy="18" r="9" stroke-dasharray="4 3" stroke-width="4"/><circle cx="54" cy="18" r="3"/><circle cx="56" cy="48" r="8" stroke-dasharray="4 3" stroke-width="4"/><circle cx="56" cy="48" r="3"/></svg>
  <p>Lorem ipsum dolor sit amet, consectetur adipiscing elit, sed do eiusmod tempor incididunt ut labore et dolore magna aliqua.</p>
  <span class="btn">Read more</span>
</article>

<section class="clients abs" role="img" aria-label="Faded office scene with a smiling businessman behind the client list"></section>
<h2 class="section-title abs" style="top:1272px">Our <b>Clients</b></h2>
<div class="chev abs" style="left:114px;top:1384px;font-size:22px">‹</div>
<div class="chev abs" style="left:1074px;top:1384px;font-size:22px">›</div>
<div class="client-row abs">
  <span><i class="sq"></i>Norvik</span><span>HALDEN PRYCE</span><span>Ostrel</span><span>Verano Capital</span><span>Selwyn</span>
</div>

<h2 class="story-title abs">Our Story</h2>
<p class="story-text abs">q7v Corp is a Ardentix and Tallowbine IT Solution Provider. We provide support for Desktops, Laptops, Tablets, Mobile Devices, Networking, WiFi, Server, Design and more by providing Remote and OnSite Support Services. q7v Corp, (Quick 7 Venture) Full service one atop shop service provider. Our CEO and Founder Lane Fosker has been working with Tallowbine Solutions all the way back to DX-OS and all the way to Tallowbine's full solution offerings of today. He trains his team to be clones of his highly technical mindset of " can do it all aptitude" because he feels nothing in technology is cut and dry, as each client and each technology work uniquely!</p>
<span class="btn abs" style="left:110px;top:1994px">Read more</span>
<div class="story-image abs" role="img" aria-label="Two colleagues in business attire looking at a tablet in an office"></div>

<h2 class="section-title abs" style="top:2112px;font-weight:400">Blog</h2>

<article class="blog-card abs" style="left:110px">
  <div class="blog-image" role="img" aria-label="Woman working on a laptop in a bright office" style="background:linear-gradient(135deg,#c9a27a,#6f6458 60%,#3b3a3c)"></div>
  <div class="date-badge abs">11<small>JUL</small></div>
  <h4>Finibus Bonorum et Malorum</h4>
  <p>Dignissimos et ducimus atque qui blanditiis praesentium voluptatum deleniti et quas.</p>
  <div class="blog-meta">👤 Ryan Tolbec &nbsp;|&nbsp; 💬 0 Comments &nbsp;<span class="more">More »</span></div>
</article>
<article class="blog-card abs" style="left:447px">
  <div class="blog-image" role="img" aria-label="Open-plan office with staff at desks" style="background:linear-gradient(180deg,#d0d0cc,#8e8f8d 55%,#4d4b48)"></div>
  <h4>Finibus Bonorum et Malorum</h4>
  <p>Dignissimos et ducimus atque qui blanditiis praesentium voluptatum deleniti et quas.</p>
  <div class="blog-meta">👤 Ryan Tolbec &nbsp;|&nbsp; 💬 0 Comments &nbsp;<span class="more">More »</span></div>
</article>
<article class="blog-card abs" style="left:787px">
  <div class="blog-image" role="img" aria-label="Businessman with a laptop looking up at a cloudy sky" style="background:linear-gradient(180deg,#5e7fa3,#c6d2dc 60%,#7f9a5a)"></div>
  <h4>Finibus Bonorum et Malorum</h4>
  <p>Dignissimos et ducimus atque qui blanditiis praesentium voluptatum deleniti et quas.</p>
  <div class="blog-meta">👤 Ryan Tolbec &nbsp;|&nbsp; 💬 0 Comments &nbsp;<span class="more">More »</span></div>
</article>

<footer class="site-footer abs">
  <div class="footer-head abs" style="left:110px;top:48px">Quick Links</div>
  <div class="quick-links abs" style="left:110px;top:90px">
    <div>Our Service</div><div>About Us</div><div>Services</div><div>Companies</div><div>Blog</div><div>Testimonials</div><div>Contact Us</div>
  </div>
  <div class="footer-head abs" style="left:336px;top:48px">Testimonials</div>
  <p class="footer-small abs" style="left:336px;top:80px;width:200px">"Lorem ipsum dolor sit amet, no fastidii expetenda sed. Ex vel zril principes, eos ad audiam scripta facilisis. Reque omittantur in per, mollis accumsan"</p>
  <p class="footer-small abs" style="left:336px;top:180px">- Mira Kells</p>
  <div class="footer-head abs" style="left:696px;top:48px">Contact Us</div>
  <svg class="abs" style="left:696px;top:86px" width="12" height="14" viewBox="0 0 12 14"><path d="M6 14 C2 9 1 7 1 5 a5 5 0 0 1 10 0 c0 2 -1 4 -5 9Z" fill="#fff"/><circle cx="6" cy="5" r="2" fill="var(--footer)"/></svg>
  <p class="footer-small abs" style="left:724px;top:82px">4120 Alder Row St.<br>Fernhill, OH 40010</p>
  <svg class="abs" style="left:696px;top:144px" width="12" height="12" viewBox="0 0 12 12"><path d="M2 1 L4.5 1 L5.5 4 L4 5 C5 7 6 8 8 8.5 L9 7 L12 8 L12 10.5 C6 11 1 6 2 1Z" fill="#fff"/></svg>
  <p class="footer-small abs" style="left:724px;top:140px">1-800 555 0142</p>
  <svg class="abs" style="left:696px;top:184px" width="13" height="10" viewBox="0 0 13 10"><rect x=".5" y=".5" width="12" height="9" fill="none" stroke="#fff"/><path d="M.5 .5 L6.5 5.5 L12.5 .5" fill="none" stroke="#fff"/></svg>
  <p class="footer-small abs" style="left:724px;top:180px">hello@q7v.host</p>
  <div class="footer-head abs" style="left:946px;top:48px">Social</div>
  <div class="social abs" style="left:946px;top:86px">Vox</div>
  <div class="social abs" style="left:992px;top:86px">Kin</div>
  <div class="social abs" style="left:1038px;top:86px">Lum</div>
  <div class="footer-brand abs">q7v Corp</div>
</footer>
<div class="bottom-bar abs">© 2018 . www.q7v.host</div>

</body>
</html>
```